Business Card Design

Business Card for professional consulting firm working with large financial institutions.

Target Market(s)

Executive buyers

Industry/Entity Type

Banking

Contact Information for Business Card

Mild creativity wanted. Not boring, but do elaborate artwork.

Font styles to use
Serif
Sans Serif

Colors

Designer to choose colors to be used in the design.

Requirements
Must have
• Standard business card features - company name, individual name, telephone, website, email, locations.
Nice to have
• Two colors
Should not have
• too many colors, fancy printing, cartoons.

```html
<!DOCTYPE html>
<html lang="en">
<head>
<meta charset="utf-8">
<title>Northledger Business Card</title>
<link rel="stylesheet" href="https://fonts.googleapis.com/css2?family=Lato:wght@400;700&display=swap">
<style>
  :root {
    --backdrop: #444444;
    --card-light: #f3f3f3;
    --card-dark: #000000;
    --ink-dark: #111111;
    --ink-light: #ffffff;
  }
  html, body {
    margin: 0;
    padding: 0;
    width: 1200px;
    height: 900px;
    overflow: hidden;
    background: var(--backdrop);
    font-family: "Lato", Arial, sans-serif;
  }
  .canvas {
    position: relative;
    width: 1200px;
    height: 900px;
  }
  .card {
    position: absolute;
    top: 200px;
    width: 310px;
    height: 502px;
    box-sizing: border-box;
  }
  .card--front {
    left: 253px;
    background: var(--card-light);
    color: var(--ink-dark);
    border-radius: 60px 0 60px 0;
  }
  .card--back {
    left: 627px;
    background: var(--card-dark);
    color: var(--ink-light);
    border-radius: 0 60px 0 60px;
  }
  .brand {
    position: absolute;
    left: 0;
    right: 0;
    display: flex;
    align-items: center;
    justify-content: center;
    gap: 10px;
    font-size: 30px;
    font-weight: 400;
    letter-spacing: 0.5px;
  }
  .brand__dot {
    width: 12px;
    height: 12px;
    border-radius: 50%;
    background: currentColor;
  }
  .card--front .brand { top: 140px; }
  .card--back .brand { top: 230px; }
  .person {
    position: absolute;
    left: 34px;
    top: 310px;
  }
  .person__name {
    margin: 0;
    font-size: 18px;
    font-weight: 400;
    letter-spacing: 0.3px;
    text-transform: uppercase;
  }
  .person__role {
    margin: 1px 0 0;
    font-size: 14px;
  }
  .contact {
    list-style: none;
    margin: 14px 0 0;
    padding: 0;
    font-size: 14px;
    line-height: 19px;
  }
  .contact__item {
    display: flex;
    align-items: center;
    gap: 5px;
  }
  .contact__icon {
    width: 11px;
    height: 11px;
    fill: var(--ink-dark);
  }
  .address {
    margin: 10px 0 0;
    font-size: 14px;
    line-height: 17px;
    font-style: normal;
  }
  .card__web {
    position: absolute;
    left: 0;
    right: 0;
    top: 439px;
    text-align: center;
    font-size: 13px;
    letter-spacing: 0.6px;
  }
</style>
</head>
<body>
<main class="canvas">
  <section class="card card--front" aria-label="Card front">
    <div class="brand"><span class="brand__dot"></span>northledger</div>
    <div class="person">
      <h1 class="person__name">Daniel Hartley</h1>
      <p class="person__role">Managing Director</p>
      <ul class="contact">
        <li class="contact__item">
          <svg class="contact__icon" viewBox="0 0 12 12" aria-hidden="true"><path d="M1 4c0-2 2-3 5-3s5 1 5 3l-2 1-1-1.5H4L3 5zM3 6h6l1.5 5h-9z"/></svg>
          044-555 018 240
        </li>
        <li class="contact__item">
          <svg class="contact__icon" viewBox="0 0 12 12" aria-hidden="true"><path d="M0 2.5h12v7H0zM0.8 3.2 6 7l5.2-3.8" stroke="#f3f3f3" stroke-width="0.8"/></svg>
          hello@northledger.com
        </li>
        <li class="contact__item">
          <svg class="contact__icon" viewBox="0 0 12 12" aria-hidden="true"><circle cx="6" cy="6" r="5.5"/><path d="M6 .5v11M.5 6h11M6 .5c-3 3-3 8 0 11M6 .5c3 3 3 8 0 11" stroke="#f3f3f3" stroke-width="0.7" fill="none"/></svg>
          www.northledger.com
        </li>
      </ul>
      <address class="address">48 Meridian Quay, Suite 9<br>Harbourton, 560218.</address>
    </div>
  </section>
  <section class="card card--back" aria-label="Card back">
    <div class="brand"><span class="brand__dot"></span>northledger</div>
    <p class="card__web">www.northledger.com</p>
  </section>
</main>
</body>
</html>
```